Life Coaching Business Card

Please check out my website at www.lorettavanbrekel.example. Ideally I would like to use the same colors that I used on the site to match my business cards i.e: pink, green, teal, white
I want the final design to include a picture of me and also to be appealing and eye catching. For the picture I submitted, you can crop it smaller to just have my face (exclude my chest) showing.
Business
Contact Information for Business Card
Loretta Vanbrekel
Transformational Life Coach
web: www.lorettavanbrekel.example
email: loretta@lorettavanbrekel.example
Phone: 555-318-7062

```html
<!DOCTYPE html>
<html lang="en">
<head>
<meta charset="utf-8">
<title>Loretta Vanbrekel – Business Card</title>
<link href="https://fonts.googleapis.com/css2?family=Libre+Baskerville:wght@700&family=Open+Sans:wght@400;600&display=swap" rel="stylesheet">
<style>
  :root {
    --page: #ffffff;
    --night: #121314;
    --dusk: #3a3c3e;
    --mist: #8a8d90;
    --band-light: #d9dadb;
    --ink: #1d1d1f;
    --green: #8cc63f;
    --green-deep: #6fae2a;
    --green-soft: #9fd056;
    --pink: #c2189a;
    --pink-bright: #e13bb8;
    --white: #ffffff;
    --column: rgba(180, 182, 185, 0.55);
  }
  * { box-sizing: border-box; margin: 0; padding: 0; }
  html, body { width: 940px; height: 1200px; overflow: hidden; background: var(--page); }
  .canvas { position: relative; width: 940px; height: 1200px; }

  .card { position: absolute; left: 120px; width: 726px; overflow: hidden; background: var(--night); }
  .card--front { top: 126px; height: 442px; }
  .card--back { top: 607px; height: 395px; }

  .scenery {
    position: absolute; inset: 0;
    background:
      radial-gradient(ellipse at 70% 35%, rgba(140,142,145,0.55), transparent 55%),
      linear-gradient(180deg, #2b2d2f 0%, #4a4c4f 40%, #1a1b1c 70%, #0d0d0e 100%);
  }
  .portrait {
    position: absolute; left: 0; top: 0; width: 190px; height: 442px;
    background: linear-gradient(90deg, #6d6f72 0%, #b9bbbe 45%, #8d8f92 75%, rgba(40,40,42,0) 100%);
  }

  .name-band {
    position: absolute; left: 170px; right: 0; top: 138px; height: 72px;
    background: linear-gradient(90deg, rgba(230,231,232,0.85), var(--band-light) 60%, rgba(200,201,203,0.9));
  }
  .name {
    position: absolute; left: 190px; top: 147px; width: 520px; text-align: center;
    font-family: "Libre Baskerville", Georgia, serif; font-weight: 700;
    font-size: 44px; color: var(--ink); letter-spacing: 0.5px; white-space: nowrap;
  }
  .title-band {
    position: absolute; left: 175px; top: 215px; width: 500px; height: 38px;
    background: linear-gradient(90deg, var(--green-soft), var(--green) 70%, rgba(140,198,63,0.2));
  }
  .title {
    position: absolute; left: 175px; top: 222px; width: 490px; text-align: center;
    font-family: "Open Sans", Arial, sans-serif; font-weight: 600; font-size: 23px;
    color: var(--white); letter-spacing: 1px;
  }
  .web-band {
    position: absolute; left: 180px; top: 258px; width: 500px; height: 42px;
    background: linear-gradient(90deg, var(--pink-bright), var(--pink) 70%, rgba(194,24,154,0.2));
  }
  .web {
    position: absolute; left: 180px; top: 266px; width: 490px; text-align: center;
    font-family: "Libre Baskerville", Georgia, serif; font-size: 20px; color: var(--white);
    font-weight: 400;
  }

  .icon-column { position: absolute; left: 124px; top: 0; width: 98px; height: 395px; background: var(--column); }
  .divider { position: absolute; left: 220px; top: 0; width: 4px; height: 395px; background: #0c0c0c; }
  .info-panel { position: absolute; left: 224px; top: 0; width: 372px; height: 395px; background: var(--green); }
  .info-row { position: absolute; left: 224px; width: 372px; }
  .info-row--name { top: 0; height: 95px; }
  .info-row--phone { top: 97px; height: 98px; background: var(--green-soft); }
  .info-row--email { top: 197px; height: 96px; background: var(--green); }
  .info-row--web { top: 295px; height: 100px; background: var(--green-soft); }
  .info-row::after { content: ""; position: absolute; left: 0; right: 0; bottom: -2px; height: 2px; background: rgba(255,255,255,0.35); }

  .label {
    position: absolute; left: 24px; font-family: "Open Sans", Arial, sans-serif;
    font-size: 27px; color: var(--ink);
  }
  .detail {
    position: absolute; left: 24px; font-family: "Open Sans", Arial, sans-serif;
    font-size: 18px; color: var(--white); white-space: nowrap;
  }
  .detail::before {
    content: ""; display: inline-block; margin-right: 12px; vertical-align: middle;
    border-left: 7px solid var(--white); border-top: 5px solid transparent; border-bottom: 5px solid transparent;
  }
  .holder {
    position: absolute; left: 24px; top: 56px; font-family: "Libre Baskerville", Georgia, serif;
    font-weight: 700; font-size: 19px; color: var(--white); letter-spacing: 1px; white-space: nowrap;
  }
  .holder::before {
    content: ""; display: inline-block; margin-right: 10px; vertical-align: middle;
    border-left: 7px solid var(--ink); border-top: 5px solid transparent; border-bottom: 5px solid transparent;
  }
  .icon { position: absolute; left: 150px; width: 46px; height: 40px; }
</style>
</head>
<body>
<main class="canvas">

  <section class="card card--front" aria-label="Business card front">
    <div class="scenery" role="img" aria-label="Dark black and white photograph of an open road under a cloudy sky"></div>
    <div class="portrait" role="img" aria-label="Black and white portrait photograph of Loretta Vanbrekel"></div>
    <div class="name-band"></div>
    <h1 class="name">Loretta Vanbrekel</h1>
    <div class="title-band"></div>
    <p class="title">TRANSFORMATIONAL LIFE COACH</p>
    <div class="web-band"></div>
    <p class="web">www.lorettavanbrekel.example</p>
  </section>

  <section class="card card--back" aria-label="Business card back">
    <div class="scenery" role="img" aria-label="Dark black and white photograph of a road and hills under clouds"></div>
    <div class="icon-column"></div>

    <svg class="icon" style="top:28px" viewBox="0 0 46 40" aria-hidden="true">
      <circle cx="23" cy="13" r="9" fill="#c9cacc"/>
      <path d="M7 38 Q7 24 23 24 Q39 24 39 38 Z" fill="#c9cacc"/>
    </svg>
    <svg class="icon" style="top:128px" viewBox="0 0 46 40" aria-hidden="true">
      <rect x="4" y="7" width="38" height="26" fill="#c9cacc"/>
      <path d="M4 7 L23 22 L42 7" fill="none" stroke="#a4a6a8" stroke-width="2"/>
    </svg>
    <svg class="icon" style="top:226px" viewBox="0 0 46 40" aria-hidden="true">
      <ellipse cx="23" cy="17" rx="19" ry="12" fill="#c9cacc"/>
      <path d="M12 25 L9 36 L20 28 Z" fill="#c9cacc"/>
    </svg>
    <svg class="icon" style="top:326px" viewBox="0 0 46 40" aria-hidden="true">
      <path d="M10 32 Q2 32 3 25 Q4 18 12 19 Q14 9 24 10 Q33 11 34 19 Q43 19 43 26 Q43 32 36 32 Z" fill="#c9cacc"/>
    </svg>

    <div class="divider"></div>
    <div class="info-panel"></div>

    <div class="info-row info-row--name">
      <p class="holder">LORETTA VANBREKEL</p>
    </div>
    <div class="info-row info-row--phone">
      <p class="label" style="top:10px">Contact me</p>
      <p class="detail" style="top:54px">555-318-7062</p>
    </div>
    <div class="info-row info-row--email">
      <p class="label" style="top:8px">Email</p>
      <p class="detail" style="top:52px">loretta@lorettavanbrekel.example</p>
    </div>
    <div class="info-row info-row--web">
      <p class="label" style="top:10px">Web</p>
      <p class="detail" style="top:52px">www.lorettavanbrekel.example</p>
    </div>
  </section>

</main>
</body>
</html>
```